Residential & commercial landscaping company

Updated business cards for commercial and landscaping company. We would like to keep out logo, but just need a more updated business card.

```html
<!DOCTYPE html>
<html lang="en">
<head>
<meta charset="utf-8">
<title>VerdantReach Business Card</title>
<link href="https://fonts.googleapis.com/css2?family=Arimo:wght@400;700&family=Libre+Baskerville:wght@700&display=swap" rel="stylesheet">
<style>
  :root {
    --bg: #2e2e2e;
    --card-white: #ffffff;
    --mist: #ececec;
    --green-bright: #3ecf3e;
    --green-mid: #1fa52c;
    --green-deep: #0c7a22;
    --green-dark: #076628;
    --green-light-text: #4fe04f;
    --ink: #111111;
    --ink-soft: #2b2b2b;
  }
  * { box-sizing: border-box; margin: 0; padding: 0; }
  html, body { width: 1200px; height: 866px; overflow: hidden; }
  body {
    background: var(--bg);
    display: flex;
    flex-direction: column;
    align-items: center;
    justify-content: center;
    gap: 40px;
    font-family: "Arimo", Arial, sans-serif;
  }
  .card {
    position: relative;
    width: 620px;
    height: 354px;
    overflow: hidden;
    box-shadow: 0 10px 24px rgba(0,0,0,0.45);
  }

  /* Front */
  .card-front { background: var(--card-white); }
  .front-foliage {
    position: absolute;
    inset: 0;
    background:
      radial-gradient(ellipse 48% 42% at 30% 18%, var(--mist) 0%, rgba(236,236,236,0.6) 55%, rgba(255,255,255,0) 100%),
      radial-gradient(ellipse 30% 40% at 12% 55%, rgba(236,236,236,0.7) 0%, rgba(255,255,255,0) 100%);
  }
  .corner-stripes {
    position: absolute;
    left: 0; top: 56px;
  }
  .contact-block {
    position: absolute;
    left: 34px; top: 62px;
  }
  .person-name {
    font-family: "Libre Baskerville", "Times New Roman", serif;
    font-weight: 700;
    font-size: 23px;
    color: var(--green-bright);
    letter-spacing: 0.5px;
  }
  .person-title {
    font-size: 13px;
    color: var(--ink-soft);
    margin: 4px 0 12px 2px;
  }
  .contact-list { list-style: none; }
  .contact-list li {
    display: flex;
    align-items: center;
    gap: 8px;
    font-size: 14px;
    color: var(--ink-soft);
    line-height: 19px;
    white-space: nowrap;
  }
  .contact-list svg { width: 13px; height: 13px; flex: none; }

  .brand-lockup {
    position: absolute;
    right: 40px; top: 224px;
    display: flex;
    align-items: center;
    gap: 12px;
  }
  .brand-mark {
    width: 34px; height: 34px;
    background: var(--green-deep);
  }
  .brand-name {
    font-family: "Arimo", Arial, sans-serif;
    font-weight: 700;
    font-size: 42px;
    color: var(--ink);
    letter-spacing: -0.5px;
  }

  /* Back */
  .card-back {
    background: linear-gradient(160deg, var(--green-bright) 0%, var(--green-mid) 40%, var(--green-deep) 100%);
  }
  .back-foliage {
    position: absolute;
    inset: 0;
    background:
      radial-gradient(ellipse 40% 35% at 35% 40%, rgba(7,102,40,0.28) 0%, rgba(7,102,40,0) 100%),
      radial-gradient(ellipse 35% 40% at 72% 62%, rgba(7,102,40,0.25) 0%, rgba(7,102,40,0) 100%);
  }
  .back-brand {
    position: absolute;
    inset: 0;
    display: flex;
    align-items: center;
    justify-content: center;
    font-family: "Arimo", Arial, sans-serif;
    font-weight: 700;
    font-size: 64px;
    color: var(--green-light-text);
    letter-spacing: -0.5px;
  }
</style>
</head>
<body>

  <section class="card card-front" aria-label="Business card front">
    <div class="front-foliage" role="img" aria-label="Faint grey photograph of tree canopy"></div>

    <svg class="corner-stripes" width="30" height="34" viewBox="0 0 30 34" aria-hidden="true">
      <polygon points="0,0 12,0 0,22" fill="var(--green-dark)"/>
      <polygon points="14,0 20,0 0,34 0,26" fill="var(--green-mid)"/>
      <polygon points="22,0 30,14 10,34 4,34" fill="var(--green-bright)"/>
    </svg>

    <div class="contact-block">
      <h1 class="person-name">Daniel Harlow Jr.</h1>
      <p class="person-title">Project Manager</p>
      <ul class="contact-list">
        <li>
          <svg viewBox="0 0 16 16" aria-hidden="true"><path d="M4 1 L6.5 4 L5 6 C6 8.5 7.5 10 10 11 L12 9.5 L15 12 L13 15 C7 15 1 9 1 3 Z" fill="var(--green-bright)"/></svg>
          555-214-0380 ext.412
        </li>
        <li>
          <svg viewBox="0 0 16 16" aria-hidden="true"><rect x="4" y="1" width="8" height="5" fill="var(--green-bright)"/><rect x="1" y="6" width="14" height="6" fill="var(--green-bright)"/><rect x="4" y="11" width="8" height="4" fill="var(--green-deep)"/></svg>
          555-730-2268
        </li>
        <li>
          <svg viewBox="0 0 16 16" aria-hidden="true"><rect x="1" y="3" width="14" height="10" fill="var(--green-bright)"/><path d="M1 3 L8 9 L15 3" stroke="#fff" stroke-width="1.4" fill="none"/></svg>
          dan@VerdantReachLandscapes.com
        </li>
      </ul>
    </div>

    <div class="brand-lockup">
      <span class="brand-mark" aria-hidden="true"></span>
      <span class="brand-name">VerdantReach</span>
    </div>
  </section>

  <section class="card card-back" aria-label="Business card back">
    <div class="back-foliage" role="img" aria-label="Faint tree silhouettes in darker green"></div>
    <div class="back-brand">VerdantReach</div>
  </section>

</body>
</html>
```